3 Page Design for Ninth Bay Capital

We want a Home Page, About Page, and Products & Services Page for Ninth Bay Capital. Please refer to the attached docs for more info.
If done in Figma, would like Figma files that can easily be ported to Wordpress.

```html
<!DOCTYPE html>
<html lang="en">
<head>
<meta charset="utf-8">
<title>Ninth Bay Capital — Home</title>
<link rel="stylesheet" href="https://fonts.googleapis.com/css2?family=Inter+Tight:wght@600;700;800&family=Inter:wght@400;500;600&display=swap">
<style>
:root{
  --purple:#6b5592;
  --crimson:#9b1b30;
  --bronze:#8b7355;
  --sand:#ebe1d0;
  --mist:#f7f7f7;
  --ink:#2b2b2b;
  --muted:#8a8a8a;
  --white:#ffffff;
}
*{margin:0;padding:0;box-sizing:border-box}
html,body{width:1200px;height:2949px;overflow:hidden}
body{position:relative;background:var(--white);font-family:"Inter",Arial,sans-serif;color:var(--ink)}
.abs{position:absolute}
.curve{position:absolute;left:0;width:1200px;display:block}

/* header */
.site-header{position:absolute;top:0;left:0;width:1200px;height:66px;background:var(--white);z-index:5}
.main-nav a{position:absolute;top:22px;font-size:15.5px;font-weight:500;color:var(--ink);text-decoration:none}
.main-nav .active{color:var(--purple)}
.brand-badge{position:absolute;left:554px;top:6px;width:92px;height:92px;border-radius:50%;background:var(--white);box-shadow:0 2px 6px rgba(0,0,0,.08);display:flex;align-items:center;justify-content:center;text-align:center;font-family:"Inter Tight",Arial,sans-serif;font-weight:700;font-size:13px;line-height:1.15;color:var(--ink);z-index:6;padding:0 10px}
.btn{position:absolute;display:flex;align-items:center;justify-content:center;gap:10px;border-radius:30px;color:var(--white);font-family:"Inter Tight",Arial,sans-serif;font-weight:700;font-size:15.5px;text-decoration:none}
.btn-crimson{background:var(--crimson)}
.btn-purple{background:var(--purple)}
.btn svg{flex:none}

/* hero */
.hero{position:absolute;top:66px;left:0;width:1200px;height:600px;background:linear-gradient(180deg,#d9d8ec 0%,#ece3ea 45%,#f3e4dc 100%)}
.hero-photo{position:absolute;left:620px;top:60px;width:560px;height:520px;background:radial-gradient(ellipse at 55% 50%,#4d6f86 0%,#7a8fa3 40%,rgba(230,220,230,0) 72%)}
.hero-title{position:absolute;left:144px;top:170px;font-family:"Inter Tight",Arial,sans-serif;font-weight:800;font-size:57px;line-height:70px;letter-spacing:-2.2px;color:var(--ink)}
.hero-text{position:absolute;left:144px;top:322px;width:450px;font-size:18px;line-height:29px;color:var(--ink)}
.slider-dots{position:absolute;left:580px;top:581px;display:flex;gap:6px}
.slider-dots span{width:10px;height:10px;border-radius:50%;border:1.5px solid var(--ink)}
.slider-dots .on{background:var(--purple);border-color:var(--purple)}

/* shared headings */
.section-title{position:absolute;left:0;width:1200px;text-align:center;font-family:"Inter Tight",Arial,sans-serif;font-weight:700;font-size:37px;letter-spacing:-1.2px;color:var(--ink)}
.rule{position:absolute;height:3px;background:var(--purple)}
.body-copy{position:absolute;font-size:15px;line-height:24px;color:var(--muted)}

/* about */
.about-band{position:absolute;left:0;top:1090px;width:1200px;height:400px;background:var(--mist)}
.about-mark{position:absolute;left:183px;top:1093px;width:372px;height:373px;display:flex;flex-direction:column;align-items:center;justify-content:center;gap:22px}
.about-mark .dot{width:200px;height:200px;border-radius:50%;background:#d8d3c8}
.about-mark .name{font-family:"Inter Tight",Arial,sans-serif;font-weight:700;font-size:34px;color:var(--ink);letter-spacing:-1px}
.about-title{position:absolute;left:633px;top:1140px;font-family:"Inter Tight",Arial,sans-serif;font-weight:700;font-size:37px;letter-spacing:-1.2px}

/* products */
.products-band{position:absolute;left:0;top:1480px;width:1200px;height:820px;background:var(--sand)}
.service-card{position:absolute;top:1696px;width:287px;height:462px;border-radius:144px;background:var(--white);text-align:center}
.service-card.featured{background:var(--purple);color:var(--white)}
.service-photo{position:absolute;left:10px;top:12px;width:266px;height:266px;border-radius:50%}
.service-name{position:absolute;left:0;top:296px;width:100%;font-size:16.5px;font-weight:500}
.service-desc{position:absolute;left:28px;top:322px;width:231px;font-size:14px;line-height:24px;color:var(--muted)}
.featured .service-desc{color:#efeaf6}
.service-link{position:absolute;left:0;top:410px;width:100%;display:flex;justify-content:center;align-items:center;gap:10px;font-family:"Inter Tight",Arial,sans-serif;font-weight:700;font-size:15px;color:var(--bronze)}
.featured .service-link{color:var(--white)}

/* footer */
.site-footer{position:absolute;left:0;top:2600px;width:1200px;height:349px;background:var(--bronze)}
.footer-brand{position:absolute;left:0;top:2662px;width:1200px;display:flex;flex-direction:column;align-items:center;gap:12px}
.footer-brand .dot{width:54px;height:54px;border-radius:50%;background:var(--white)}
.footer-brand .name{font-family:"Inter",Arial,sans-serif;font-weight:600;font-size:18px;color:var(--white);letter-spacing:.5px}
.footer-nav{position:absolute;left:0;top:2794px;width:1200px;display:flex;justify-content:center;gap:26px;font-size:15px;font-weight:500;color:var(--white)}
.footer-nav span{color:var(--white)}
.footer-divider{position:absolute;left:165px;top:2837px;width:870px;height:1px;background:rgba(255,255,255,.3)}
.copyright{position:absolute;left:0;top:2859px;width:1200px;text-align:center;font-size:14px;color:var(--white)}
.social{position:absolute;top:2900px;width:28px;height:28px;border-radius:50%;background:var(--white)}
.social.active{background:var(--crimson)}
</style>
</head>
<body>

<header class="site-header">
  <nav class="main-nav">
    <a class="active" style="left:143px" href="#">Home</a>
    <a style="left:226px" href="#">About Us</a>
    <a style="left:332px" href="#">Products &amp; Services</a>
  </nav>
  <div class="brand-badge">Ninth Bay Capital</div>
  <a class="btn btn-crimson" href="#" style="left:839px;top:10px;width:216px;height:44px;font-size:15px;gap:6px">
    <svg width="13" height="13" viewBox="0 0 24 24"><path fill="#fff" d="M6.6 10.8a15 15 0 0 0 6.6 6.6l2.2-2.2c.3-.3.7-.4 1-.2 1.1.4 2.3.6 3.6.6.6 0 1 .4 1 1V20c0 .6-.4 1-1 1A17 17 0 0 1 3 4c0-.6.4-1 1-1h3.5c.6 0 1 .4 1 1 0 1.3.2 2.5.6 3.6.1.3 0 .7-.2 1z"/></svg>
    Call Us 1-800-555-0142
  </a>
</header>

<section class="hero">
  <div class="hero-photo" role="img" aria-label="Photo of two athletes stretching outdoors against an evening sky"></div>
</section>
<h1 class="hero-title">Where Discipline<br>Meets Wealth</h1>
<p class="hero-text">Technical Refined’ positions NBC at the intersection of performance and sophistication.</p>
<a class="btn btn-purple" href="#" style="left:144px;top:411px;width:225px;height:47px;font-size:16.5px">Book a Consultation
  <svg width="17" height="17" viewBox="0 0 20 20"><circle cx="10" cy="10" r="10" fill="#fff"/><path d="M5.5 10h8M10 6l4 4-4 4" stroke="#6b5592" stroke-width="2" fill="none" stroke-linecap="round" stroke-linejoin="round"/></svg></a>
<div class="slider-dots"><span></span><span class="on"></span><span></span></div>
<svg class="curve" style="top:500px" height="170" viewBox="0 0 1200 170">
  <path d="M0 30 Q600 200 1200 30 L1200 170 L0 170Z" fill="#8b7355"/>
  <path d="M0 40 Q600 230 1200 40 L1200 170 L0 170Z" fill="#fff"/>
</svg>

<section class="mission">
  <h2 class="section-title" style="top:714px">Our Mission</h2>
  <div class="rule" style="left:564px;top:775px;width:73px"></div>
  <p class="body-copy" style="left:100px;top:797px;width:1000px;text-align:center">NBC bridges the worlds of performance, wealth, and wellness&nbsp; helping athletes and entrepreneurs build lasting success on and off the field.<br>It merges the discipline of sports, the structure of business, and the power of automation to create generational success.</p>
  <a class="btn btn-crimson" href="#" style="left:528px;top:882px;width:144px;height:42px;font-size:15px">Learn More
    <svg width="16" height="16" viewBox="0 0 20 20"><circle cx="10" cy="10" r="10" fill="#fff"/><path d="M5.5 10h8M10 6l4 4-4 4" stroke="#9b1b30" stroke-width="2" fill="none" stroke-linecap="round" stroke-linejoin="round"/></svg></a>
</section>

<svg class="curve" style="top:980px" height="120" viewBox="0 0 1200 120">
  <path d="M0 123 Q600 -100 1200 123Z" fill="#f7f7f7"/>
</svg>
<section class="about-band"></section>
<div class="about-mark"><div class="dot"></div><div class="name">Ninth Bay Capital</div></div>
<h2 class="about-title">About&nbsp; Ninth Bay Capital</h2>
<div class="rule" style="left:633px;top:1197px;width:72px"></div>
<p class="body-copy" style="left:634px;top:1229px;width:430px;font-size:14px;line-height:23.5px">Technical Refined’ positions NBC at the intersection of performance and sophistication.The design system communicates trust, discipline, and modernity aligning perfectly with NBC’s mission to help athletes and entrepreneurs create generational success.</p>
<a class="btn btn-crimson" href="#" style="left:634px;top:1354px;width:208px;height:43px;font-size:15px">Learn More About Us
  <svg width="16" height="16" viewBox="0 0 20 20"><circle cx="10" cy="10" r="10" fill="#fff"/><path d="M5.5 10h8M10 6l4 4-4 4" stroke="#9b1b30" stroke-width="2" fill="none" stroke-linecap="round" stroke-linejoin="round"/></svg></a>

<section class="products-band"></section>
<svg class="curve" style="top:1470px" height="160" viewBox="0 0 1200 160">
  <path d="M0 10 Q600 155 1200 10 L1200 0 L0 0Z" fill="#8b7355"/>
  <path d="M0 6 Q600 135 1200 6 L1200 0 L0 0Z" fill="#f7f7f7"/>
</svg>
<h2 class="section-title" style="top:1606px">Products &amp; Services</h2>
<div class="rule" style="left:563px;top:1666px;width:73px"></div>

<article class="service-card" style="left:144px">
  <div class="service-photo" role="img" aria-label="Photo of athletes running together in a stadium" style="background:linear-gradient(160deg,#8d8e92,#5b5d63 55%,#b06d5e)"></div>
  <h3 class="service-name">Athlete Transition Program</h3>
  <p class="service-desc">Lorem ipsum dolor sit consectetur adipiscing elit, sed do eiusmod tempor minim veniam,</p>
  <div class="service-link">Learn More <svg width="15" height="15" viewBox="0 0 20 20"><circle cx="10" cy="10" r="10" fill="#8b7355"/><path d="M5.5 10h8M10 6l4 4-4 4" stroke="#fff" stroke-width="2" fill="none" stroke-linecap="round" stroke-linejoin="round"/></svg></div>
</article>
<article class="service-card featured" style="left:458px">
  <div class="service-photo" role="img" aria-label="Photo of a woman breathing freely outdoors with open arms" style="background:linear-gradient(160deg,#3f6a7a,#6f8f96 50%,#9aa7b4)"></div>
  <h3 class="service-name">Performance Wealth System</h3>
  <p class="service-desc">Lorem ipsum dolor sit consectetur adipiscing elit, sed do eiusmod tempor minim veniam,</p>
  <div class="service-link">Learn More <svg width="15" height="15" viewBox="0 0 20 20"><circle cx="10" cy="10" r="10" fill="#fff"/><path d="M5.5 10h8M10 6l4 4-4 4" stroke="#6b5592" stroke-width="2" fill="none" stroke-linecap="round" stroke-linejoin="round"/></svg></div>
</article>
<article class="service-card" style="left:771px">
  <div class="service-photo" role="img" aria-label="Photo of a coach guiding a client through a yoga pose" style="background:linear-gradient(160deg,#dcdfe6,#b9a49a 50%,#3a4f8a)"></div>
  <h3 class="service-name">Wellness &amp; Continuity Coaching</h3>
  <p class="service-desc">Lorem ipsum dolor sit consectetur adipiscing elit, sed do eiusmod tempor minim veniam,</p>
  <div class="service-link">Learn More <svg width="15" height="15" viewBox="0 0 20 20"><circle cx="10" cy="10" r="10" fill="#8b7355"/><path d="M5.5 10h8M10 6l4 4-4 4" stroke="#fff" stroke-width="2" fill="none" stroke-linecap="round" stroke-linejoin="round"/></svg></div>
</article>

<svg class="curve" style="top:2140px" height="170" viewBox="0 0 1200 170">
  <path d="M0 142 Q600 10 1200 142 L1200 170 L0 170Z" fill="#8b7355"/>
  <path d="M0 152 Q600 26 1200 152 L1200 170 L0 170Z" fill="#fff"/>
</svg>

<section class="cta">
  <h2 class="section-title" style="top:2315px;font-size:38px">Ready to Build a Life That Performs Beyond the Field?</h2>
  <div class="rule" style="left:564px;top:2371px;width:72px"></div>
  <p class="body-copy" style="left:150px;top:2399px;width:900px;text-align:center">Lorem ipsum dolor sit amet, consectetur adipiscing elit, sed do eiusmod tempor incididunt ut labore et dolore magna aliqua. Ut enim ad minim veniam, quis nostrud exercitation ullamco laboris nisi ut aliquip ex ea commodo consequat.</p>
  <a class="btn btn-crimson" href="#" style="left:496px;top:2481px;width:207px;height:43px;font-size:15px">Book a Consultation
    <svg width="16" height="16" viewBox="0 0 20 20"><circle cx="10" cy="10" r="10" fill="#fff"/><path d="M5.5 10h8M10 6l4 4-4 4" stroke="#9b1b30" stroke-width="2" fill="none" stroke-linecap="round" stroke-linejoin="round"/></svg></a>
</section>

<svg class="curve" style="top:2570px" height="160" viewBox="0 0 1200 160">
  <path d="M0 130 Q600 -92 1200 130 L1200 160 L0 160Z" fill="#ebe1d0"/>
  <path d="M0 142 Q600 -62 1200 142 L1200 160 L0 160Z" fill="#8b7355"/>
</svg>
<footer class="site-footer"></footer>
<div class="footer-brand"><div class="dot"></div><div class="name">NINTH BAY CAPITAL</div></div>
<nav class="footer-nav">
  <span>HOME</span><span>|</span><span>ABOUT US</span><span>|</span><span>PRODUCTS &amp; SERVICES</span><span>|</span><span>CONTACT</span>
</nav>
<div class="footer-divider"></div>
<p class="copyright">© 2025 Ninth Bay Capital -&nbsp; All Rights Reserved</p>
<a class="social" href="#" aria-label="Social profile 1" style="left:533px"></a>
<a class="social" href="#" aria-label="Social profile 2" style="left:568px"></a>
<a class="social active" href="#" aria-label="Video channel" style="left:602px"></a>
<a class="social" href="#" aria-label="Social profile 3" style="left:636px"></a>

</body>
</html>
```